Blood Testing Health App

We are looking for a graphics designer to create a web app for us so that we may insert it into a health management website system.
For branding purposes we are at www.Vantiqor.com and we are revamping our website... Example of new colors attached.
How we work...
We are a blood testing company based in the USA.
We offer a blood testing service nationwide in the USA.
We allow customers to order tests directly from us, visit a lab, have their blood drawn, or submit a urine sample, the lab tests it and they send the results back to our computer system and we share it with the customer.
The benefits of this are the customer does not need to go to the doctor and pay for the doctors visit to order these tests, which save them money. The tests are cheaper than going through the doctor. The customer simply uses us to get the test and the results and they can then take the results to their doctor... this process has saved them money. Others may be interested in regular check ups for blood work etc... and this allows them to do it with out needing a doctor, or if you have no insurance, this is a cheaper option too. We are quicker than a doctor, customers do not need appointments etc.
Hopefully you now have a better understanding as to what we do.
Here is the spec.
The app screen size is 750 px wide by 700 px high. ( A pdf is attached to show where the app is going to go, it is on page 3 of the pdf) The customer will have the ability to scroll… therefore the length of the page can be longer.
The app will consist of the following sections
Entry Page –
This will be the first page the user sees upon opening the app. This will be where they are directed from to the sections of the app discussed below. This needs to be branded for VantiQor with a modern look.
1 – Order Test (Giving them the ability to purchase a blood test within the app)
2 – VantiQor Dashboard (A dashboard that has everything they could need to use our service_
How it works Section on entry page – this will be a simple set of graphics showing how the service works. We already have the graphics for this, they do not need to be built again. They are attached to this brief
Basic structure of sections –
Order Test –
This page contains all tests, filed in categories – and Sub categories – Each test needs a link to an Information section – Price – Buy Now – Cart Process
VantiQor Dashboard –
A page of icons along the top of the app
- My Confirmation
- My Nearest Lab
- My Receipt
- My Orders
- My Account
- My Results
- My Inbox
- Contact Us
Sections in more detail -
Order A Test –
Show all categories/ sub categories – There are 23 categories, 14 sub categories, and within these categories are 300 tests - Here is the information for the categories etc - http://www.vantiqor.com/panels.aspx?PanelGroupID=4 Just in case it helps :)
We need to present this in a graphic format that is spacious, modern (brimlake, kivvo web appearance is the direction we are going for) We need it to be clear and not overwhelming to the customer.
Functionality idea…
Customer clicks category/ subcategory and tests appear.
Customer sees small 35 word description. For more information the test opens into a lightbox or expand the container which ever graphic designer believes to be most visually appealing
Buy Now must always be visible, along with price of the test
Buying process explained – Customer clicks buy now –
They are then taken to a Review Order screen ( This contains Order summary and choose payment method – insert payment details )
– Confirm payment –
Confirmation screen appears, thanking them.
They are then taken to the VantiQor Dashboard...
VantiQor Dashboard –
"My Confirmation" - Print Confirmation Order (PDF is in brief, we want this web based not a pdf download)
"My Nearest Lab Location" - This does not need to be designed because the web developer has this part under control, but we do need the icon in the dashboard
"My Receipt" - Print receipt - This does not exist in our system yet. So we need to create this from scratch - It will need to have - The test they are purchasing and the amount of the test - The customers name - The order ID - Must provide printer friendly option too
"My Orders" - This will have a list of orders - At the end of each order will be a status update of either "Test results" "Open order"
A graphic table format would be perfect. This will be linked to relevant results if they have been received. I have also attached a version of what the customer currently sees on our website. We know it is nasty ;) We are redesigning... but the information is there for this section to help design it with the right info. If the results are ready it will say in this list.
"Results Ready" will be a link to show those results once the customer has clicked the link, and the results will appear in the app, under the icons. There must be a printer friendly version too.
"My Results" Developer will sort this page out but we need the icon... It will be exactly like my orders but only show test results
"My Account" - This will be a place for them to update their personal information - Name, DOB, Address, Email Address
"My Inbox" - An inbox interface - Our way of contacting the customer for promotions we are running etc – We need a design of how this screen will appear. We also need the icon in the dashboard to have a notification on it if there are messages in the customers inbox. A little red 1, or circle with number of messages in the inbox.
"Customer Service" - This does not need to be designed because the web developer has this part under control, but we do need the icon in the dashboard
Icons appear along the top of app ( example - Mac icons/ iphone app icons) When the customer clicks an icon the content always appears below the icons
Here is more information for the icons and what should appear when each icon is clicked.
Screens to be designed –
Entry Page
Order A Test Page
Review Order Screen/Payment Screen - Show a lightbox that shows payment has been confirmed. Customer clicks close and are on the Confirmation Screen
VantiQor Dashboard - Screens mentioned in detail above
We can't wait to see your designs!
Please email any questions.
Hi all this is the first time we have used pixel harbor and understand the budget was too low for this project. We have now increased the budget to $2,000 and extended the deadline by another week
Hi all we are receiving some really great designs. I just added an example of the space that the web app will be going into... It is called "morvelapp.pdf"
Hi guys updated the brief. Hopefully this will help with the dashboard part of the design

```html
<!DOCTYPE html>
<html lang="en">
<head>
<meta charset="utf-8">
<title>VantiQor – My Order</title>
<link rel="stylesheet" href="https://fonts.googleapis.com/css2?family=Open+Sans:wght@400;600;700&display=swap">
<style>
  :root {
    --orange: #ff7f00;
    --orange-dark: #e86a00;
    --green: #8ca41b;
    --green-dark: #6f8a0c;
    --green-light: #a9c22c;
    --text: #333333;
    --rule: #c9cfa8;
    --page: #ffffff;
    --header-bg: #f4f4f2;
  }
  * { box-sizing: border-box; margin: 0; padding: 0; }
  html, body { width: 692px; height: 1200px; overflow: hidden; background: var(--page); }
  body { font-family: "Open Sans", sans-serif; color: var(--text); position: relative; }

  .brand-bar { position: absolute; top: 0; left: 0; width: 692px; height: 132px; background: var(--header-bg);
    display: flex; align-items: center; justify-content: center; }
  .brand-name { font-size: 42px; font-weight: 600; color: var(--text); }

  .page-title { position: absolute; top: 132px; left: 0; width: 692px; height: 92px; background: var(--orange);
    color: #fff; font-size: 38px; font-weight: 600; display: flex; align-items: center; justify-content: center; }

  .order-head { position: absolute; top: 224px; left: 0; width: 692px; height: 83px; background: var(--green);
    color: #fff; font-size: 30px; }
  .order-head span { position: absolute; top: 50%; transform: translateY(-50%); }

  .col-item { left: 42px; }
  .col-price { left: 344px; }
  .col-remove { left: 540px; }

  .order-row { position: absolute; left: 0; width: 692px; border-bottom: 2px solid var(--rule); font-size: 27px; }
  .order-row .cell { position: absolute; top: 50%; transform: translateY(-50%); line-height: 1.35; }
  .row-1 { top: 307px; height: 131px; }
  .row-2 { top: 438px; height: 127px; }
  .row-subtotal { top: 565px; height: 104px; border-bottom: none; }
  .subtotal-label { color: var(--orange); font-weight: 600; }

  .remove-box { position: absolute; left: 577px; top: 50%; transform: translateY(-50%);
    width: 35px; height: 35px; border: 2px solid #8d8d8d; background: #fff; }
  .remove-box.is-checked { border-color: var(--orange); }

  .promo-input { position: absolute; top: 671px; left: 69px; width: 554px; height: 56px;
    border: 2px solid #9a9a9a; background: #fff; }

  .btn { position: absolute; display: flex; align-items: center; justify-content: center;
    color: #fff; font-weight: 600; border-radius: 3px; }
  .btn-apply { top: 752px; left: 224px; width: 235px; height: 67px; font-size: 36px;
    background: linear-gradient(var(--green-light), var(--green-dark)); border: 2px solid var(--green-dark); }
  .btn-orange { left: 108px; width: 466px; height: 67px; font-size: 33px;
    background: linear-gradient(#ff9a2e, var(--orange-dark)); border: 2px solid #d86000; }
  .btn-checkout { top: 971px; }
  .btn-more { top: 1066px; }

  .total-row { position: absolute; top: 852px; left: 0; width: 692px; height: 82px;
    border-top: 2px solid var(--rule); border-bottom: 2px solid var(--rule);
    color: var(--green); font-size: 30px; font-weight: 600; }
  .total-row span { position: absolute; top: 50%; transform: translateY(-50%); }
  .total-amount { font-weight: 700; }

  .footer-stripe { position: absolute; top: 1172px; left: 0; width: 692px; height: 28px; display: flex; }
  .footer-stripe i { flex: 1; display: block; }
</style>
</head>
<body>
  <header class="brand-bar">
    <span class="brand-name">VantiQor</span>
  </header>

  <h1 class="page-title">My Order</h1>

  <div class="order-head">
    <span class="col-item">Items</span>
    <span class="col-price">Price</span>
    <span class="col-remove">Remove</span>
  </div>

  <div class="order-row row-1">
    <span class="cell col-item">Thyroid Panel II:<br>T4 &amp; T3 with TSH</span>
    <span class="cell col-price">$105.00</span>
    <span class="remove-box is-checked">
      <svg width="31" height="31" viewBox="0 0 31 31"><path d="M9 8 L22 23 M22 8 L9 23" stroke="#ff7f00" stroke-width="3.2" stroke-linecap="round"/></svg>
    </span>
  </div>

  <div class="order-row row-2">
    <span class="cell col-item">Comprehensive Food<br>Allergy Profile</span>
    <span class="cell col-price">$540.00</span>
    <span class="remove-box"></span>
  </div>

  <div class="order-row row-subtotal">
    <span class="cell col-item subtotal-label">Subtotal</span>
    <span class="cell col-price">$645.00</span>
  </div>

  <div class="promo-input" aria-label="Promo code"></div>
  <div class="btn btn-apply">Apply</div>

  <div class="total-row">
    <span class="col-item">Total</span>
    <span class="col-price total-amount">$645.00</span>
  </div>

  <div class="btn btn-orange btn-checkout">Proceed to Checkout</div>
  <div class="btn btn-orange btn-more">Order More Tests</div>

  <footer class="footer-stripe">
    <i style="background:#6f8a0c"></i><i style="background:#8ca41b"></i><i style="background:#7a9612"></i>
    <i style="background:#a9c22c"></i><i style="background:#8ca41b"></i><i style="background:#b8cf3a"></i>
    <i style="background:#9bb322"></i><i style="background:#c6da4a"></i>
  </footer>
</body>
</html>
```